****Business Card Design for Quarrystone Development. Design based around attached logo/company name

I’m looking for business card design for my company Quarrystone Development Group,LLC. Design should be professional, sharp and minimal. Outside of the attached logos, greyscale colors for remainder of cards. My thoughts are two-sided card with attached logo on one side and my info on the other but open to one-sided as well with right design.
Target Market(s)
Real estate professionals including banks, private investors, property owners, developers, commercial tenants like Brewlantern, Grovika or Tanquist’s.
Industry/Entity Type
Commercial real estate development and investments.
Contact Information for Business Card
Name, title, email, phone #’s, web address and physical address
Font styles to use
Other font styles liked:
- Helvetica, Garamond, etc
Colors
Designer to choose only greyscale colors for use in the design.
Requirements
Must have
- Attached logo first or second options.
Nice to have
- Two sided card with logo on one side. Attached Logo/company name can be laid out any way that flows as long as it’s legible.name
Should not have
- No loud colors. ***Please do not include logo, I have removed the company design with a logo image.

```html
<!DOCTYPE html>
<html lang="en">
<head>
<meta charset="utf-8">
<title>Quarrystone Development Group, LLC — Business Cards</title>
<link href="https://fonts.googleapis.com/css2?family=Marcellus&family=Roboto:wght@400&family=Tinos&display=swap" rel="stylesheet">
<style>
  :root {
    --backdrop: #2c2c2c;
    --card-light: #f4f4f4;
    --card-mid: #e6e6e8;
    --ink: #4b4f5c;
    --ink-soft: #5a5d66;
    --rule: #6b6f7a;
  }
  * { margin: 0; padding: 0; box-sizing: border-box; }
  html, body { width: 1200px; height: 1138px; overflow: hidden; }
  body { background: var(--backdrop); position: relative; }

  .card {
    position: absolute;
    width: 620px;
    height: 375px;
    border-radius: 16px;
    background: linear-gradient(135deg, var(--card-light) 0%, var(--card-mid) 100%);
    overflow: hidden;
  }
  .card--front { left: 272px; top: 184px; }
  .card--back  { left: 274px; top: 606px; }

  .wordmark {
    font-family: "Marcellus", serif;
    color: var(--ink);
    font-weight: 400;
    text-transform: uppercase;
    line-height: 1;
  }
  .wordmark__name { display: block; letter-spacing: 1px; }
  .wordmark__group { display: block; letter-spacing: 2.4px; }

  .card--front .wordmark {
    position: absolute;
    left: 0; right: 0;
    top: 150px;
    text-align: center;
  }
  .card--front .wordmark__name { font-size: 38px; }
  .card--front .wordmark__group { font-size: 15.5px; margin-top: 12px; }

  .front-web {
    position: absolute;
    left: 0; right: 0;
    top: 334px;
    display: flex;
    align-items: center;
    justify-content: center;
    gap: 16px;
    font-family: "Roboto", sans-serif;
    font-size: 14px;
    color: var(--ink-soft);
  }
  .front-web__rule {
    width: 70px;
    height: 2px;
    background: linear-gradient(90deg, transparent, var(--rule), transparent);
  }

  .card--back .wordmark {
    position: absolute;
    right: 30px;
    top: 44px;
    text-align: right;
  }
  .card--back .wordmark__name { font-size: 36px; }
  .card--back .wordmark__group { font-size: 15px; margin-top: 10px; }

  .contact {
    position: absolute;
    right: 30px;
    top: 160px;
    text-align: right;
    font-family: "Tinos", serif;
    color: var(--ink);
  }
  .contact__person {
    font-family: "Marcellus", serif;
    font-size: 23px;
    letter-spacing: 0.5px;
    text-transform: uppercase;
  }
  .contact__title { font-size: 14px; margin-top: 4px; }
  .contact__address { font-size: 15px; line-height: 22px; margin-top: 20px; padding-right: 26px; }
  .contact__list { list-style: none; font-size: 15px; margin-top: 4px; }
  .contact__item {
    display: flex;
    justify-content: flex-end;
    align-items: center;
    gap: 10px;
    height: 23px;
  }
  .contact__icon { width: 14px; height: 14px; fill: var(--ink-soft); }
</style>
</head>
<body>

  <section class="card card--front" aria-label="Card front">
    <div class="wordmark">
      <span class="wordmark__name">Quarrystone</span>
      <span class="wordmark__group">Development Group, LLC</span>
    </div>
    <div class="front-web">
      <span class="front-web__rule"></span>
      <span>www.yourwebsite.com</span>
      <span class="front-web__rule"></span>
    </div>
  </section>

  <section class="card card--back" aria-label="Card back">
    <div class="wordmark">
      <span class="wordmark__name">Quarrystone</span>
      <span class="wordmark__group">Development Group, LLC</span>
    </div>

    <div class="contact">
      <div class="contact__person">John Doe Smith</div>
      <div class="contact__title">Managing Director</div>
      <div class="contact__address">234 Anywhere St., Any City,<br>Any Town, US 123456</div>
      <ul class="contact__list">
        <li class="contact__item">828-111-1111
          <svg class="contact__icon" viewBox="0 0 16 16" aria-hidden="true"><path d="M2 5c0-2 2-3 6-3s6 1 6 3v1h-3V5H5v1H2zM4 7h8l2 6H2z"/></svg>
        </li>
        <li class="contact__item">john@yourwebsite.com
          <svg class="contact__icon" viewBox="0 0 16 16" aria-hidden="true"><path d="M1 3h14v10H1zM2 4l6 5 6-5v-.2H2z" fill-rule="evenodd"/></svg>
        </li>
        <li class="contact__item">www.yourwebsite.com
          <svg class="contact__icon" viewBox="0 0 16 16" aria-hidden="true"><circle cx="8" cy="8" r="6.5" fill="none" stroke="#5a5d66" stroke-width="1.4"/><path d="M1.5 8h13M8 1.5v13" stroke="#5a5d66" stroke-width="1.2"/><ellipse cx="8" cy="8" rx="3" ry="6.5" fill="none" stroke="#5a5d66" stroke-width="1.2"/></svg>
        </li>
      </ul>
    </div>
  </section>

</body>
</html>
```